Public Speaking Book for aspiring, ambitious speakers

I'm looking for a 6x9 book cover (Brivora standard) as well as ebook and audiobook formats.

I'm looking for orange font on a white background as these are my brand colours.

Feel free to use some yellow and gold too if you deem it appropriate.

Title: Climb and Kindle
Subtitle: Find Your Voice. Tell Your Story. Share your Message.
Author: Owen Thistlewood

I would like to have a picture of a female speaker on the front cover.

Alternatively, some kind of image that symbolises public speaking like a microphone, podium etc

Target Market(s)

Aspiring professional speakers

Colors
f78f20

Requirements
Must have
• Correct spelling!
Nice to have
• A logo or picture that fits the theme, but no pressure if you can't think of anything
Should not have
• No men in suits please. I don't want this to have a 1980s corporate look.

```html
<!DOCTYPE html>
<html lang="en">
<head>
<meta charset="utf-8">
<title>Climb and Kindle — Owen Thistlewood</title>
<link rel="stylesheet" href="https://fonts.googleapis.com/css2?family=Open+Sans:wght@400;700&display=swap">
<style>
  :root {
    --paper: #ffffff;
    --flame: #f78f20;
    --gold: #fcd27e;
  }
  html, body {
    margin: 0;
    padding: 0;
    width: 840px;
    height: 1200px;
    overflow: hidden;
    background: var(--paper);
  }
  .cover {
    position: relative;
    width: 840px;
    height: 1200px;
    background: var(--paper);
    color: var(--flame);
    font-family: "Open Sans", Arial, sans-serif;
    overflow: hidden;
  }
  .title {
    margin: 0;
    font-weight: inherit;
  }
  .title-word,
  .tagline,
  .author-name {
    position: absolute;
    left: 0;
    width: 100%;
    text-align: center;
    line-height: 1;
    margin: 0;
    white-space: nowrap;
  }
  .title-word {
    font-size: 216px;
    font-weight: 700;
    letter-spacing: -0.03em;
  }
  .title-word--first { top: 78px; }
  .title-word--middle { top: 344px; }
  .title-word--last { top: 612px; }

  .subtitle {
    margin: 0;
  }
  .tagline {
    font-size: 30px;
    font-weight: 400;
    letter-spacing: 0.22em;
    text-indent: 0.22em;
    text-transform: uppercase;
  }
  .tagline--one { top: 314px; }
  .tagline--two { top: 574px; }
  .tagline--three { top: 861px; }

  .author-band {
    position: absolute;
    left: 0;
    top: 1092px;
    width: 840px;
    height: 36px;
  }
  .author-bar {
    position: absolute;
    top: 0;
    height: 36px;
    width: 150px;
  }
  .author-bar--left {
    left: 0;
    background: linear-gradient(to right, var(--gold), var(--flame));
  }
  .author-bar--right {
    right: 0;
    background: linear-gradient(to left, var(--gold), var(--flame));
  }
  .author-name {
    top: 1090px;
    font-size: 38px;
    font-weight: 400;
    letter-spacing: 0.18em;
    text-indent: 0.18em;
    text-transform: uppercase;
  }
</style>
</head>
<body>
  <main class="cover">
    <h1 class="title">
      <span class="title-word title-word--first">CLIMB</span>
      <span class="title-word title-word--middle">AND</span>
      <span class="title-word title-word--last">KINDLE</span>
    </h1>
    <p class="subtitle">
      <span class="tagline tagline--one">Find Your Voice.</span>
      <span class="tagline tagline--two">Tell Your Story.</span>
      <span class="tagline tagline--three">Share your Message.</span>
    </p>
    <div class="author-band" aria-hidden="true">
      <span class="author-bar author-bar--left"></span>
      <span class="author-bar author-bar--right"></span>
    </div>
    <p class="author-name">Owen Thistlewood</p>
  </main>
</body>
</html>
```